Systems and Technology Consultants - Website

Design & Build a website for a new company which operates in the Systems and Technology space for Transportation, Government and Commercial sectors.

Overall design should be minimalist in nature.
Should also have a feed that provides news and event updates on the main page.
Logo has already been awarded and should be incorporated into the site.

We like the overall layout, functionality and simplicity of the below sites. Submitted designs could be similar to or a combination of the aspects on these sites, or perhaps a whole different concept - we are open to new ideas.
Norvique.com
Teblo.it

Update 1 Dated 27 May 2014

All I am moving away from the Teblo.it website and would like it to be more aligned with Norvique.com not only in layout but in functionality. I will be extending the deadline of this design brief for two weeks to incorporate additional requirements and will add addtional funding to the project.

Apologies for not having more information available to provide but with so many submissions its getting confusing.

Thanks Derek

Please note that the brief has been updated and the deadline has been extended.

Important: We will need two language versions of the website, English and Arabic; the website is hosted on HostPelican

Hello All, Thank you for your submissions. We have narrowed it down to the final 6 designers and I just wanted to take a moment and provide a bit of feedback regarding the concepts that we like and the modifications we are looking for. First, let me mention some of the design functions we like. - At the top of the homepage we really like the "region" or "language" tab so that the website can be viewed in both English and Arabic. - We like the homepage to have clear color variation so that the different sections of the homepage are distinct. Additionally, we like the bottom portion of the homepage to be in red. We feel that draws attention to our contact information. Again, we would like the colors to integrate black, gray-scale, red, etc. - Having a search tab at the top of the home page, or integrated into the main image, so that the site is easy to navigate. - We especially like the main image to have the scrolling tabs at the bottom so it is easy to browse the services offered (Consultancy, Solutions Architecture, Masters Systems Integration, Independent Design Review). - In regards to the services offered tab we really like the idea that a few people presented that have the outside of our logo with an icon in the middle of consultancy, solutions, etc., etc. Secondly, as mentioned in our brief we really enjoy the design of norvique site. Specially, we enjoy the strong iconic images they use, the way the tabs at the top scroll easily, and contact us page that generates an email. Lastly, I've included some photos of the concept we have been working on. What we are trying to demonstrate is how our company offers a range of services that are essentially linked together. We provide individual services that when combined present the full service package. We would like this concept to be integrated into the over concept of our website. Please feel free to ask for clarification of any of the above points or contact us if you have any additional questions. We appreciate all of your hard work and are very excited to see the updated designs. Best, Marta Vennick Quelbrant Senior Program Manager marta.vennick@quelbrant-example.com

Industry/Entity Type

Government

Font styles to use
Serif
Sans Serif

Requirements
Must have
• Must work on/adapt to various/mobile devices (responsive)
Must be simple and straightforward
Colors should be in line/matching with logo
2 language versions: English and Arabic (no Thai)
Services should be the first group/row of items after/below the main image
Note: the website will be hosted by hostpelican
Nice to have
• Submit feedback form
What's New section
The banner at the bottom of the site should not be too large; we would like a narrow one more
It would be nice if the header/top banner (with Home, About, etc. tabs) could stay in place as you scroll down (like Norvique and Chatterloop)
We will likely only use one image with a Company slogan on the Home page rather than a carousel of images to rotate through
Should not have
• This is the existing website: http://www.quelbrant-example.org
We do not like the animation, the way the banner icons/titles bounce
Not simple enough, we don't like the functionality or how pages load so slowly
We do not like the logo centered - it should be at the left
The banner and its tabs should not be towards the right, we would like them to be centered, to go all the way across and to be below the logo

```html
<!DOCTYPE html>
<html lang="en">
<head>
<meta charset="utf-8">
<title>Quelbrant – Home</title>
<link rel="stylesheet" href="https://fonts.googleapis.com/css2?family=Roboto:wght@400;500;700&family=Roboto+Condensed:wght@400;700&display=swap">
<style>
  :root {
    --red: #e2222a;
    --ink: #555555;
    --ink-soft: #8a8a8a;
    --nav: #666666;
    --page: #f5f5f5;
    --band: #ebebeb;
    --footer: #e6e6e6;
    --rule: #d4d4d4;
    --card: #f7f7f7;
    --card-border: #d8d8d8;
    --dark: #1d1d1d;
  }
  * { box-sizing: border-box; margin: 0; padding: 0; }
  html, body { width: 960px; height: 1200px; overflow: hidden; }
  body {
    position: relative;
    background: var(--page);
    font-family: "Roboto", Arial, sans-serif;
    color: var(--ink);
  }

  /* Header */
  .site-header {
    position: absolute; left: 0; top: 0; width: 960px; height: 99px;
    background: var(--page); border-bottom: 1px solid #dcdcdc;
  }
  .brand {
    position: absolute; left: 148px; top: 38px;
    display: flex; align-items: center; gap: 8px;
  }
  .brand-mark { width: 14px; height: 14px; background: var(--red); }
  .brand-name {
    font-size: 19px; font-weight: 700; letter-spacing: 2px;
    color: var(--red); text-transform: uppercase;
  }
  .main-nav a {
    position: absolute; top: 42px; font-size: 11.5px; color: var(--nav);
    text-decoration: none; white-space: nowrap;
  }
  .main-nav a.is-active { color: var(--red); }
  .main-nav a.is-active::after {
    content: ""; position: absolute; left: 0; right: 0; top: 17px;
    height: 2px; background: var(--red);
  }

  /* Hero */
  .hero { position: absolute; left: 0; top: 99px; width: 960px; height: 282px; overflow: hidden; }
  .hero-photo {
    position: absolute; inset: 0;
    background:
      linear-gradient(180deg, rgba(255,255,255,.18) 0%, rgba(255,255,255,0) 40%, rgba(0,0,0,.08) 100%),
      linear-gradient(90deg, #a9a9a9 0%, #8f8f8f 20%, #9e9e9e 40%, #b4b4b4 58%, #d2d2d2 72%, #dedede 80%, #a4a4a4 92%, #8c8c8c 100%);
  }
  .hero-title {
    position: absolute; left: 150px; top: 41px; width: 349px; height: 54px;
    background: var(--dark); color: #e9e9e9;
    font-family: "Roboto", Arial, sans-serif; font-weight: 700;
    font-size: 43px; line-height: 54px; padding-left: 14px; letter-spacing: -.6px;
    white-space: nowrap;
  }
  .service-list { position: absolute; left: 149px; top: 117px; list-style: none; }
  .service-list li { display: flex; height: 21px; margin-bottom: 3.5px; }
  .service-tick {
    width: 24px; height: 21px; background: var(--red);
    display: flex; align-items: center; justify-content: center;
  }
  .service-name {
    width: 88px; margin-left: 3px; background: var(--dark); color: #f0f0f0;
    font-family: "Roboto Condensed", Arial, sans-serif; font-weight: 700;
    font-size: 13.5px; line-height: 21px; padding-left: 7px;
  }
  .hero-arrow {
    position: absolute; top: 123px; width: 35px; height: 35px;
    background: rgba(60,60,60,.55); display: flex; align-items: center; justify-content: center;
  }
  .hero-arrow.prev { left: 8px; }
  .hero-arrow.next { left: 917px; background: rgba(40,40,40,.5); }

  /* Sections */
  .section-title {
    position: absolute; left: 148px; font-size: 21px; font-weight: 500; color: #6a6a6a;
  }
  .section-title .bracket { color: var(--red); }
  .view-all {
    position: absolute; right: 148px; font-size: 11.5px; color: var(--nav); text-decoration: none;
  }
  .read-more {
    font-size: 10px; font-weight: 500; color: var(--red); text-decoration: none;
  }

  .news { position: absolute; left: 0; top: 381px; width: 960px; height: 372px; background: var(--band); border-bottom: 2px solid var(--rule); }
  .news .section-title { top: 37px; }
  .news .view-all { top: 46px; }
  .news-card {
    position: absolute; top: 104px; width: 155px; height: 225px;
    background: var(--card); border: 1px solid var(--card-border);
  }
  .news-card .thumb { height: 85px; }
  .news-card h3 { position: absolute; left: 8px; top: 95px; font-size: 12.8px; font-weight: 500; color: #666; }
  .news-card p { position: absolute; left: 8px; top: 122px; width: 138px; font-size: 9.9px; line-height: 12.6px; color: var(--ink-soft); }
  .news-card .read-more { position: absolute; left: 8px; top: 201px; }

  .events { position: absolute; left: 0; top: 753px; width: 960px; height: 345px; background: var(--page); border-bottom: 1px solid var(--rule); }
  .events .section-title { top: 40px; }
  .events .view-all { top: 49px; }
  .event-card { position: absolute; top: 105px; width: 212px; }
  .event-card .thumb { height: 71px; }
  .event-card h3 { margin-top: 11px; font-size: 12.8px; font-weight: 500; color: #666; }
  .event-card p { margin-top: 12px; font-size: 9.6px; line-height: 12.6px; color: var(--ink-soft); }
  .event-card .read-more { display: block; margin-top: 16px; }

  .site-footer { position: absolute; left: 0; top: 1098px; width: 960px; height: 102px; background: var(--footer); }
  .copyright { position: absolute; left: 148px; top: 43px; font-size: 10px; color: #666; }
  .social { position: absolute; left: 745px; top: 39px; display: flex; gap: 6px; }
  .social span { width: 18px; height: 18px; border-radius: 50%; background: #6f6f6f; }
</style>
</head>
<body>

<header class="site-header">
  <div class="brand"><span class="brand-mark"></span><span class="brand-name">Quelbrant</span></div>
  <nav class="main-nav">
    <a class="is-active" href="#" style="left:387px">Home</a>
    <a href="#" style="left:441px">Business Unit</a>
    <a href="#" style="left:539px">Services</a>
    <a href="#" style="left:609px">About Us</a>
    <a href="#" style="left:681px">Locations</a>
    <a href="#" style="left:757px">Contact Us</a>
  </nav>
</header>

<section class="hero">
  <div class="hero-photo" role="img" aria-label="Black and white city skyline with a smiling businessman in a white shirt and tie gesturing towards the services list"></div>
  <h1 class="hero-title">Services Offered</h1>
  <ul class="service-list">
    <li><span class="service-tick"><svg width="14" height="12" viewBox="0 0 14 12"><path d="M1.5 6.5 5 10 12.5 2" fill="none" stroke="#fff" stroke-width="2.4"/></svg></span><span class="service-name">Construction</span></li>
    <li><span class="service-tick"><svg width="14" height="12" viewBox="0 0 14 12"><path d="M1.5 6.5 5 10 12.5 2" fill="none" stroke="#fff" stroke-width="2.4"/></svg></span><span class="service-name">Operations</span></li>
    <li><span class="service-tick"><svg width="14" height="12" viewBox="0 0 14 12"><path d="M1.5 6.5 5 10 12.5 2" fill="none" stroke="#fff" stroke-width="2.4"/></svg></span><span class="service-name">Maintenance</span></li>
    <li><span class="service-tick"><svg width="14" height="12" viewBox="0 0 14 12"><path d="M1.5 6.5 5 10 12.5 2" fill="none" stroke="#fff" stroke-width="2.4"/></svg></span><span class="service-name">Engineering</span></li>
    <li><span class="service-tick"><svg width="14" height="12" viewBox="0 0 14 12"><path d="M1.5 6.5 5 10 12.5 2" fill="none" stroke="#fff" stroke-width="2.4"/></svg></span><span class="service-name">Consulting</span></li>
  </ul>
  <a class="hero-arrow prev" href="#" aria-label="Previous"><svg width="18" height="24" viewBox="0 0 18 24"><path d="M14 2 4 12l10 10" fill="none" stroke="#fff" stroke-width="3.5"/></svg></a>
  <a class="hero-arrow next" href="#" aria-label="Next"><svg width="18" height="24" viewBox="0 0 18 24"><path d="M4 2l10 10L4 22" fill="none" stroke="#fff" stroke-width="3.5"/></svg></a>
</section>

<section class="news">
  <h2 class="section-title"><span class="bracket">[</span>Latest News<span class="bracket">]</span></h2>
  <a class="view-all" href="#">View all</a>

  <article class="news-card" style="left:149px">
    <div class="thumb" role="img" aria-label="Portrait of a businessman in a suit beside window blinds" style="background:linear-gradient(90deg,#e6e6e6 0%,#d0d0d0 35%,#a8a8a8 70%,#7c7c7c 100%)"></div>
    <h3>Lorem Ipsum</h3>
    <p>Lorem ipsum dolor sit amet, consectetur adipisicing elit, sed do eiusmod tempor incidi-dunt ut labore et dolore magna aliqua.</p>
    <a class="read-more" href="#">Read more</a>
  </article>
  <article class="news-card" style="left:318px">
    <div class="thumb" role="img" aria-label="Presenter speaking to a seated audience in front of a screen" style="background:linear-gradient(90deg,#6a7884 0%,#cbd4da 40%,#c9c98a 72%,#9a7a5e 100%)"></div>
    <h3>Lorem Ipsum</h3>
    <p>Lorem ipsum dolor sit amet, consectetur adipisicing elit, sed do eiusmod tempor incidi-dunt ut labore et dolore magna aliqua.</p>
    <a class="read-more" href="#">Read more</a>
  </article>
  <article class="news-card" style="left:486px">
    <div class="thumb" role="img" aria-label="Colleagues in a bright office meeting" style="background:linear-gradient(90deg,#d6c4a2 0%,#ece8e2 45%,#bccde0 100%)"></div>
    <h3>Lorem Ipsum</h3>
    <p>Lorem ipsum dolor sit amet, consectetur adipisicing elit, sed do eiusmod tempor incidi-dunt ut labore et dolore magna aliqua.</p>
    <a class="read-more" href="#">Read more</a>
  </article>
  <article class="news-card" style="left:655px">
    <div class="thumb" role="img" aria-label="Group of business people applauding" style="background:linear-gradient(90deg,#22303f 0%,#6a5649 50%,#c49c84 100%)"></div>
    <h3>Lorem Ipsum</h3>
    <p>Lorem ipsum dolor sit amet, consectetur adipisicing elit, sed do eiusmod tempor incidi-dunt ut labore et dolore magna aliqua.</p>
    <a class="read-more" href="#">Read more</a>
  </article>
</section>

<section class="events">
  <h2 class="section-title"><span class="bracket">[</span>Event Updates<span class="bracket">]</span></h2>
  <a class="view-all" href="#">View all</a>

  <article class="event-card" style="left:149px">
    <div class="thumb" role="img" aria-label="Conference hall with a panel on a red stage and an audience" style="background:linear-gradient(180deg,#3c2c46 0%,#b82a22 55%,#5c2a1a 100%)"></div>
    <h3>Lorem Ipsum</h3>
    <p>Lorem ipsum dolor sit amet, consectetur adipi-sicing elit, sed do eiusmod tempor incididunt ut labore et dolore magna aliqua.consectetur adipisicing elit, sed do eiusmod tempor incidi-dunt ut labore et dolore magna aliqua.</p>
    <a class="read-more" href="#">Read more</a>
  </article>
  <article class="event-card" style="left:374px">
    <div class="thumb" role="img" aria-label="Exhibition hall with a green and blue trade stand" style="background:linear-gradient(180deg,#8e9aaa 0%,#80bf3c 55%,#3080b8 100%)"></div>
    <h3>Lorem Ipsum</h3>
    <p>Lorem ipsum dolor sit amet, consectetur adipi-sicing elit, sed do eiusmod tempor incididunt ut labore et dolore magna aliqua.consectetur adipisicing elit, sed do eiusmod tempor incidi-dunt ut labore et dolore magna aliqua.</p>
    <a class="read-more" href="#">Read more</a>
  </article>
  <article class="event-card" style="left:598px">
    <div class="thumb" role="img" aria-label="Blueprints with a tape measure, hammer and hard hat" style="background:linear-gradient(90deg,#bac8dc 0%,#dfe6f0 55%,#e8b84a 100%)"></div>
    <h3>Lorem Ipsum</h3>
    <p>Lorem ipsum dolor sit amet, consectetur adipi-sicing elit, sed do eiusmod tempor incididunt ut labore et dolore magna aliqua.consectetur adipisicing elit, sed do eiusmod tempor incidi-dunt ut labore et dolore magna aliqua.</p>
    <a class="read-more" href="#">Read more</a>
  </article>
</section>

<footer class="site-footer">
  <p class="copyright">Quelbrant © 2014, All Rights Reserved</p>
  <div class="social" aria-label="Social links"><span></span><span></span><span></span></div>
</footer>

</body>
</html>
```